Heron Dusk business card design

I make handmade colourful women's beaded jewellery (necklaces and earnings).
I require a business card to be designed to truly reflect my jewellery, that is, it is different and stands out.
I would like the business card to look creative, arty, gentle and feminine and fit in with the look of my website and logo (already developed).
I would like the business card to have strong use of the water reeds that are flowing in the wind (please see the banner image on my website www.herondusk.net and attached files).

Target Market(s)

Women who are fashion conscious, hip and funky. My audience like things that are a little different and stand out in a crowd.These women are aged in their 20's-40's.

Industry/Entity Type

Jewelry

Contact Information for Business Card

Please include the following items:
1) my logo: Heron Dusk
2) my name, address and phone number: Darla Fontenot, Sydney, Australia, 0498 315 270
3) my web details: www.herondusk.net, info@herondusk.net, www.facebook.com/herondusk

Font styles to use
Other font styles liked:
• Remachine Script

Requirements
Must have
• My business card must have the following:
• 1) my personal details including all my website contacts (see above).
• 2) Heron Dusk logo
• 3) Reeds flowing in the wind (see my banner image on my website www.herondusk.net or see attached files).
Nice to have
• A sunrise in the background (rising over water)
• I would prefer that the colour scheme to fit with the Heron Dusk logo, that is the colours of an early morning sunrise i.e yellows, oranges. The use of black and white is fine.
Should not have
• I do not like a commercial manufactured look with hard edges. I would like a look that is soft and reflects an artistic, creative and independent business.

```html
<!DOCTYPE html>
<html lang="en">
<head>
<meta charset="utf-8">
<title>Heron Dusk — Business Card</title>
<link rel="stylesheet" href="https://fonts.googleapis.com/css2?family=Open+Sans:wght@400;600;700&display=swap">
<style>
  :root {
    --bg: #e9e4dc;
    --sun-light: #fde7a0;
    --sun-mid: #f6c343;
    --sun-deep: #e09a12;
    --reed-brown: #7a4a17;
    --ink: #1c1c1c;
    --charcoal: #2b2b2b;
    --paper: #ffffff;
    --gold: #f3b41c;
    --text-light: #f2f2f2;
  }
  * { box-sizing: border-box; margin: 0; padding: 0; }
  html, body { width: 1200px; height: 950px; overflow: hidden; }
  body {
    background: var(--bg);
    font-family: "Open Sans", Arial, sans-serif;
    position: relative;
  }
  .card {
    position: absolute;
    left: 250px;
    width: 700px;
    height: 400px;
    border-radius: 22px;
    overflow: hidden;
    box-shadow: 0 6px 18px rgba(0,0,0,0.18);
  }
  .card--front { top: 60px; }
  .card--back { top: 490px; background: var(--charcoal); }

  /* Front */
  .reed-scene {
    position: absolute; inset: 0;
    background:
      radial-gradient(ellipse at 55% 55%, var(--sun-light) 0%, var(--sun-mid) 45%, var(--sun-deep) 100%);
  }
  .reed-scene::after {
    content: ""; position: absolute; inset: 0;
    background: linear-gradient(180deg, rgba(122,74,23,0.15) 0%, rgba(122,74,23,0) 40%, rgba(122,74,23,0.35) 100%);
  }
  .front-logo {
    position: absolute; left: 50%; top: 150px; transform: translateX(-50%);
    display: flex; align-items: center; gap: 14px;
  }
  .logo-dot {
    width: 70px; height: 70px; border-radius: 50%;
    background: var(--gold); border: 3px solid var(--ink);
  }
  .logo-name {
    font-weight: 600; font-size: 34px; color: var(--ink); white-space: nowrap;
  }
  .social-row {
    position: absolute; left: 50%; top: 300px; transform: translateX(-50%);
    display: flex; gap: 12px;
  }
  .social-row span {
    width: 24px; height: 24px; border-radius: 50%;
    border: 2px solid var(--paper);
  }

  /* Back */
  .back-shapes { position: absolute; inset: 0; }
  .back-logo {
    position: absolute; left: 60px; top: 165px;
    display: flex; align-items: center; gap: 12px;
  }
  .back-logo .logo-dot { width: 64px; height: 64px; }
  .back-logo .logo-name { font-size: 30px; }
  .contact {
    position: absolute; right: 28px; top: 40px; width: 300px;
    text-align: right; color: var(--text-light);
  }
  .contact__name { color: var(--gold); font-weight: 700; font-size: 22px; }
  .contact__role { font-size: 15px; margin-top: 2px; }
  .contact__place { font-size: 15px; line-height: 1.35; margin-top: 40px; margin-right: 30px; }
  .contact__list { list-style: none; margin-top: 26px; }
  .contact__list li {
    display: flex; justify-content: flex-end; align-items: center; gap: 10px;
    font-size: 15px; line-height: 1.6;
  }
  .contact__list svg { width: 18px; height: 18px; flex: none; }
</style>
</head>
<body>

<section class="card card--front" aria-label="Card front">
  <div class="reed-scene" role="img" aria-label="Silhouetted water reeds swaying in the wind against a golden sunrise"></div>
  <div class="front-logo">
    <span class="logo-dot"></span>
    <span class="logo-name">Heron Dusk</span>
  </div>
  <div class="social-row" aria-hidden="true">
    <span></span><span></span><span></span><span></span>
  </div>
</section>

<section class="card card--back" aria-label="Card back">
  <svg class="back-shapes" viewBox="0 0 700 400" preserveAspectRatio="none" aria-hidden="true">
    <path d="M0,130 C120,70 270,75 340,130 C400,200 420,300 395,400 L0,400 Z" fill="var(--gold)"/>
    <path d="M0,130 C120,70 260,82 315,140 C372,210 385,300 360,400 L0,400 Z" fill="var(--paper)"/>
  </svg>

  <div class="back-logo">
    <span class="logo-dot"></span>
    <span class="logo-name">Heron Dusk</span>
  </div>

  <div class="contact">
    <p class="contact__name">Mara Quill</p>
    <p class="contact__role">President</p>
    <p class="contact__place">Darla Fontenot<br>Sydney, Australia</p>
    <ul class="contact__list">
      <li>0498 315 270
        <svg viewBox="0 0 20 20"><path d="M5 2h3l1.5 4-2 1.5a10 10 0 0 0 5 5L14 10.5l4 1.5v3c0 1-1 2-2 2A14 14 0 0 1 3 4c0-1 1-2 2-2z" fill="var(--gold)"/></svg>
      </li>
      <li>info@herondusk.net
        <svg viewBox="0 0 20 20"><rect x="2" y="4" width="16" height="12" rx="1.5" fill="var(--gold)"/><path d="M2.5 5l7.5 6 7.5-6" stroke="var(--charcoal)" stroke-width="1.5" fill="none"/></svg>
      </li>
      <li>www.herondusk.net
        <svg viewBox="0 0 20 20"><circle cx="10" cy="10" r="8" fill="var(--gold)"/><path d="M2 10h16M10 2c3 3 3 13 0 16M10 2c-3 3-3 13 0 16" stroke="var(--charcoal)" stroke-width="1.2" fill="none"/></svg>
      </li>
      <li>herondusk
        <svg viewBox="0 0 20 20"><rect x="2" y="2" width="16" height="16" rx="2" fill="var(--gold)"/></svg>
      </li>
    </ul>
  </div>
</section>

</body>
</html>
```